Every Shelf Set Neatly or ESN Organized needs a business card design. ESN Organized is a professi

We need a business card design that is clean, sharp and conveys a sense of organization. I already have a logo.

Target Market(s)

Families (specifically mothers), small business owners, parents, seniors

Industry/Entity Type

Business

Contact Information for Business Card

My website is www.esnorganized-example.com and my Facebook page is http://www.sociallink-example.com/everyshelfsetneatly. The phone number is 418-552-7094 and I want to be listed as Lorna M. Pelham, Owner

Requirements
Must have
• My logo.

```html
<!DOCTYPE html>
<html lang="en">
<head>
<meta charset="utf-8">
<title>ESN Organized – Business Card</title>
<link rel="stylesheet" href="https://fonts.googleapis.com/css2?family=Open+Sans:wght@400;600;700&display=swap">
<style>
  :root {
    --backdrop: #e9e6e1;
    --card: #ffffff;
    --card-shade: #eceeef;
    --brand-blue: #1a85d6;
    --brand-blue-light: #4aa6ea;
    --brand-blue-dark: #0f6fbf;
    --ink: #2a2a2a;
  }
  * { box-sizing: border-box; margin: 0; padding: 0; }
  html, body {
    width: 1200px; height: 843px; overflow: hidden;
    background: var(--backdrop);
    font-family: "Open Sans", Arial, sans-serif;
  }
  .sheet {
    position: relative; width: 1200px; height: 843px;
    display: flex; align-items: center; justify-content: center; gap: 40px;
  }
  .card {
    position: relative; width: 540px; height: 309px;
    background: linear-gradient(160deg, var(--card) 55%, var(--card-shade));
    box-shadow: 0 10px 28px rgba(0,0,0,0.18);
    overflow: hidden;
  }

  /* Back: logo and tagline */
  .card-back { display: flex; flex-direction: column; align-items: center; justify-content: center; }
  .brand-lockup { display: flex; align-items: center; gap: 14px; margin-top: -20px; }
  .brand-dot { width: 30px; height: 30px; border-radius: 50%; background: var(--brand-blue); }
  .brand-name {
    font-size: 38px; font-weight: 600; color: var(--brand-blue); letter-spacing: 1px;
  }
  .tagline {
    position: absolute; bottom: 58px; left: 0; right: 0; text-align: center;
    font-size: 15px; font-weight: 600; color: var(--ink);
  }

  /* Front: name, contacts, blue band */
  .holder { position: absolute; top: 30px; left: 30px; }
  .holder-name {
    font-size: 20px; font-weight: 700; color: var(--brand-blue); letter-spacing: 0.5px;
    text-transform: uppercase;
  }
  .holder-role { font-size: 13px; color: var(--ink); text-transform: uppercase; margin-top: 1px; }

  .contact-list {
    position: absolute; top: 40px; right: 24px; list-style: none;
    display: flex; flex-direction: column; align-items: flex-end; gap: 4px;
  }
  .contact-item {
    display: flex; align-items: center; gap: 8px;
    font-size: 14px; color: var(--ink);
  }
  .contact-icon { width: 13px; height: 13px; flex: none; }

  .clip-band { position: absolute; left: 0; bottom: 0; width: 540px; height: 170px; }
</style>
</head>
<body>
<main class="sheet">

  <section class="card card-back" aria-label="Card back">
    <div class="brand-lockup">
      <span class="brand-dot"></span>
      <span class="brand-name">ESN Organized</span>
    </div>
    <p class="tagline">We keep you organized, so you stay always organized</p>
  </section>

  <section class="card card-front" aria-label="Card front">
    <div class="holder">
      <h1 class="holder-name">Lorna M. Pelham</h1>
      <p class="holder-role">Owner</p>
    </div>

    <ul class="contact-list">
      <li class="contact-item">418-552-7094
        <svg class="contact-icon" viewBox="0 0 16 16" aria-hidden="true">
          <path fill="var(--brand-blue)" d="M3.6 1.2l2.3 2.6-1.2 1.8c.9 2 2.6 3.7 4.6 4.6l1.8-1.2 2.6 2.3-1.5 2.3C7 13.6 2.4 9 1.3 2.7z"/>
        </svg>
      </li>
      <li class="contact-item">www.esnorganized-example.com
        <svg class="contact-icon" viewBox="0 0 16 16" aria-hidden="true">
          <circle cx="8" cy="8" r="7" fill="var(--brand-blue)"/>
          <path d="M1 8h14M8 1c-3 3.5-3 10.5 0 14M8 1c3 3.5 3 10.5 0 14" stroke="#fff" stroke-width="1.1" fill="none"/>
        </svg>
      </li>
      <li class="contact-item">everyshelfsetneatly
        <svg class="contact-icon" viewBox="0 0 16 16" aria-hidden="true">
          <rect x="1" y="1" width="14" height="14" rx="2" fill="var(--brand-blue)"/>
        </svg>
      </li>
    </ul>

    <svg class="clip-band" viewBox="0 0 540 170" role="img" aria-label="Large blue paperclip graphic">
      <defs>
        <linearGradient id="bandFill" x1="0" y1="0" x2="1" y2="1">
          <stop offset="0" stop-color="var(--brand-blue-dark)"/>
          <stop offset="0.45" stop-color="var(--brand-blue-light)"/>
          <stop offset="1" stop-color="var(--brand-blue)"/>
        </linearGradient>
      </defs>
      <path fill="url(#bandFill)" d="M0 40 Q20 10 80 10 L540 10 L540 170 L0 170 Z"/>
    </svg>
  </section>

</main>
</body>
</html>
```